New PowerPoint Design Project

I need a company powerpoint template for my company, Varnok (see design file logo attached), that has a number of templated slides with an exciting supporting colour palette. Needs to have header and footer sections, tables in colour which support the logo colour, bar and line charts, dot point slides and image (placeholders) slides. Logo is attached.
The primary use of this template is to pitch for new work - ie about us page, previous clients page, then a breakdown of services offered in a table format with prices etc...
Updates

Hi everyone
Please see some example PPT templates that provide more of a guide as to what I need.

Thanks
Leopold

Font styles to use
Serif
Sans Serif

Colors
0054AA
0677BA
7BADD7
CADEEF
E8F1F8
00AB8E
00BBA5
67D7C9
C6EFE9
E9F9F6
59FF00
82FF00
B8FF75
E3FFCB
F4FFEA
FFC000
F8CF3A
FAE287
FDF2CF
FEFAEE

```html
<!DOCTYPE html>
<html lang="en">
<head>
<meta charset="utf-8">
<title>Varnok Presentation Template</title>
<link rel="stylesheet" href="https://fonts.googleapis.com/css2?family=Poppins:ital,wght@0,400;0,500;0,700;0,800;1,400;1,500&family=Cormorant+Garamond:wght@500&display=swap">
<style>
:root{
  --deep:#0d3a33;
  --teal:#17564b;
  --night:#0c1614;
  --yellow:#ffc233;
  --lime:#c8d94a;
  --gold:#c9a227;
  --slate:#3c4452;
  --ink:#1c1c1c;
  --white:#ffffff;
  --grey:#9a9a9a;
  --orange:#ffa500;
}
*{margin:0;padding:0;box-sizing:border-box}
html,body{width:1200px;height:835px;overflow:hidden;background:#fff}
.board{position:absolute;left:0;top:0;width:2292px;height:1595px;transform:scale(0.52356);transform-origin:0 0;font-family:"Poppins",sans-serif}
.slide{position:absolute;width:669px;height:376px;overflow:hidden;box-shadow:0 10px 30px rgba(0,0,0,.35);color:var(--white)}
.c1{left:64px}.c2{left:813px}.c3{left:1562px}
.r1{top:100px}.r2{top:601px}.r3{top:1102px}
.photo{position:absolute;inset:0}
.brand{font-family:"Cormorant Garamond",serif;font-weight:500;color:var(--gold);letter-spacing:1px;line-height:1}
.brand-top{position:absolute;right:6px;top:4px;font-size:28px}
.abs{position:absolute}
.heading{position:absolute;left:0;right:0;text-align:center;color:var(--yellow);font-weight:700;font-size:19px}
.heading .bar{color:var(--white);font-weight:400;margin:0 8px}
.body-text{font-size:10px;line-height:17px;text-align:center}
.footer{position:absolute;left:10px;right:0;bottom:8px;height:20px;display:flex;align-items:center;font-size:9px}
.footer .globe{width:14px;height:14px;border-radius:50%;background:var(--yellow);margin-right:5px}
.footer .rule{flex:1;height:1px;background:rgba(255,255,255,.45);margin:0 12px 0 16px}
.footer .page{background:var(--yellow);color:var(--ink);font-size:8px;padding:5px 7px;margin-right:0}
.light .footer{color:var(--ink)}
.light .footer .rule{background:#bbb}
.agenda-row{position:absolute;left:304px;width:241px;height:31px;display:flex;font-size:8px}
.agenda-row .label{flex:1;background:#0b0f0e;border:1px solid #555;display:flex;align-items:center;padding-left:16px}
.agenda-row .num{width:39px;background:var(--yellow);color:var(--ink);font-weight:500;display:flex;align-items:center;justify-content:center}
.point{position:absolute;left:378px;width:280px}
.point .tick{width:22px;height:1px;background:var(--yellow);margin-bottom:6px}
.point h3{font-size:12px;font-weight:700;margin-bottom:4px}
.point p{font-size:8px;line-height:14px}
.partner-cell{position:absolute;width:140px;height:80px;display:flex;align-items:center;justify-content:center}
.badge{background:#2c2c2c}
.th{position:absolute;top:122px;height:25px;background:var(--yellow);color:var(--ink);font-size:8px;font-weight:700;display:flex;align-items:center;justify-content:center}
.row-label{position:absolute;left:60px;width:130px;text-align:center;font-size:8.5px}
.dot{position:absolute;width:7px;height:7px;border-radius:50%;background:var(--orange)}
.dot.off{background:var(--grey)}
</style>
</head>
<body>
<div class="board">

  <!-- Cover -->
  <section class="slide c1 r1" style="background:linear-gradient(135deg,#0f5a4d,#0a3a33 70%,#0d2e29)">
    <div class="photo" role="img" aria-label="Dark green sports car photo" style="left:110px;top:130px;width:460px;height:170px;inset:auto;background:radial-gradient(ellipse at 50% 55%,#1f6e62,rgba(13,58,51,0) 70%)"></div>
    <h1 class="abs" style="left:22px;top:18px;width:470px;font-size:29px;font-style:italic;font-weight:500;line-height:38px">Faerspiciatis unde omnis iste natus error sit voluptatem accusantium</h1>
    <div class="abs" style="left:527px;top:38px;font-size:12px">XX, April, 2025</div>
    <div class="abs" style="left:527px;top:60px;width:142px;height:1px;background:var(--gold)"></div>
    <div class="abs" style="left:20px;top:294px;font-size:20px;font-weight:500;color:var(--lime)">Faccusantium doloremque laudantium</div>
    <p class="abs" style="left:20px;top:330px;width:360px;font-size:8.5px;font-style:italic;line-height:15px">Farspiciatis unde omnis aseciste natus error sisaect voluptatem accusantium doloremque laudantium.</p>
    <div class="brand abs" style="right:18px;top:320px;font-size:44px">VARNOK</div>
  </section>

  <!-- Agenda -->
  <section class="slide c2 r1" style="background:var(--night)">
    <div class="photo" role="img" aria-label="Dark garage photo with a car" style="background:radial-gradient(ellipse at 40% 60%,#254a43,#0c1a17 70%)"></div>
    <div class="brand brand-top">VARNOK</div>
    <div class="abs" style="left:160px;top:174px;color:var(--yellow);font-weight:700;font-size:19px"><span style="color:#fff;font-weight:400;margin-right:8px">|</span>Agenda<span style="color:#fff;font-weight:400;margin-left:8px">|</span></div>
    <div class="agenda-row" style="top:65px"><div class="label">01.&nbsp; Agenda</div><div class="num">01</div></div>
    <div class="agenda-row" style="top:109px"><div class="label">02.&nbsp; Mision &amp; Vision</div><div class="num">02</div></div>
    <div class="agenda-row" style="top:153px"><div class="label">03.&nbsp; Our Statistics</div><div class="num">03</div></div>
    <div class="agenda-row" style="top:197px"><div class="label">04.&nbsp; Page Break</div><div class="num">04</div></div>
    <div class="agenda-row" style="top:240px"><div class="label">05.&nbsp; Perspiciatis Unde</div><div class="num">05</div></div>
    <div class="agenda-row" style="top:284px"><div class="label">06.&nbsp; What We Achieve</div><div class="num">06</div></div>
    <div class="footer"><span class="globe"></span>www.varnok.com<span class="rule"></span><span class="page">Page 02</span></div>
  </section>

  <!-- About -->
  <section class="slide c3 r1" style="background:#163d37">
    <div class="photo" role="img" aria-label="Black luxury sedan in front of a building" style="background:linear-gradient(180deg,#1f4a43,#12322d 60%,#0e2824)"></div>
    <div class="brand brand-top">VARNOK</div>
    <div class="heading" style="top:24px"><span class="bar">|</span>About Us<span class="bar">|</span></div>
    <p class="abs body-text" style="left:50px;right:50px;top:70px">Kaerspiciatis unde omnis iste natus error secsit voluptatem accusantium dolore saefmque laudantium, totam rem aperiam, eaque ipsa quae ab illo inventore veritatis secet quasi architecto beatae vitae dicta sunt explicabo. Nemo enim ipsam voluptatem quia voluptas sseit aspernatur aut odit aut fugit, sed quia consequuntur magni dolores eoscse qaseui ratione voluptatem sequi nseesciunt. Neque porro quisquam est, qui dolorem ipsum.</p>
    <div class="footer"><span class="globe"></span>www.varnok.com<span class="rule"></span><span class="page">Page 03</span></div>
  </section>

  <!-- Ideas -->
  <section class="slide c1 r2" style="background:#163b35">
    <div class="photo" role="img" aria-label="Orange sports car at night in a city" style="background:radial-gradient(ellipse at 28% 68%,#4a3a2a,#1b3d37 45%,#12302b)"></div>
    <div class="brand brand-top">VARNOK</div>
    <div class="abs" style="left:17px;top:18px;color:var(--yellow);font-weight:700;font-size:17.5px;line-height:28px"><span style="color:#fff;font-weight:400;margin-right:6px">|</span>Powerful ideas come from multiplied minds.<br><span style="margin-left:10px">We assign two partners to every client.</span><span style="color:#fff;font-weight:400;margin-left:6px">|</span></div>
    <div class="point" style="top:97px"><div class="tick"></div><h3>Find the need</h3><p>Caerspiciatis unde omnis iste natus error slaskcit voluptatem accusantium doloremque laudantium.</p></div>
    <div class="point" style="top:189px"><div class="tick"></div><h3>Hit the mark</h3><p>Caerspiciatis unde omnis iste natus error slaskcit voluptatem accusantium doloremque laudantium.</p></div>
    <div class="point" style="top:271px"><div class="tick"></div><h3>Look ahead</h3><p>Caerspiciatis unde omnis iste natus error slaskcit voluptatem accusantium doloremque laudantium.</p></div>
    <div class="footer"><span class="globe"></span>www.varnok.com<span class="rule"></span><span class="page">Page 04</span></div>
  </section>

  <!-- Graph -->
  <section class="slide c2 r2" style="background:#173a35">
    <div class="photo" role="img" aria-label="Dark showroom photo with a car" style="background:radial-gradient(ellipse at 50% 70%,#23463f,#142f2b 70%)"></div>
    <div class="brand brand-top">VARNOK</div>
    <div class="heading" style="top:28px"><span class="bar">|</span>Graph<span class="bar">|</span></div>
    <p class="abs body-text" style="left:150px;right:150px;top:73px">Caerspiciatis unde omnis iste natus error slaskcit voluptatem accusantium doloremque laudantium.</p>
    <svg class="abs" style="left:0;top:0" width="669" height="376" viewBox="0 0 669 376">
      <g fill="#fff" font-size="10" font-family="Poppins,sans-serif" text-anchor="end">
        <text x="122" y="137">100</text><text x="122" y="176">80</text><text x="122" y="215">60</text>
        <text x="122" y="254">40</text><text x="122" y="293">20</text><text x="122" y="327">0</text>
      </g>
      <line x1="140" y1="328" x2="570" y2="328" stroke="#5a6a66" stroke-width="2"/>
      <g>
        <rect x="149" y="133" width="31" height="192" fill="var(--yellow)"/><rect x="149" y="261" width="31" height="64" fill="var(--slate)"/>
        <rect x="188" y="133" width="31" height="192" fill="var(--yellow)"/><rect x="188" y="230" width="31" height="95" fill="var(--slate)"/>
        <rect x="227" y="133" width="31" height="192" fill="var(--yellow)"/><rect x="227" y="193" width="31" height="132" fill="var(--slate)"/>
        <rect x="266" y="133" width="31" height="192" fill="var(--yellow)"/><rect x="266" y="218" width="31" height="107" fill="var(--slate)"/>
        <rect x="305" y="133" width="31" height="192" fill="var(--yellow)"/><rect x="305" y="170" width="31" height="155" fill="var(--slate)"/>
        <rect x="344" y="133" width="31" height="192" fill="var(--yellow)"/><rect x="344" y="261" width="31" height="64" fill="var(--slate)"/>
        <rect x="383" y="133" width="31" height="192" fill="var(--yellow)"/><rect x="383" y="196" width="31" height="129" fill="var(--slate)"/>
        <rect x="422" y="133" width="31" height="192" fill="var(--yellow)"/><rect x="422" y="230" width="31" height="95" fill="var(--slate)"/>
        <rect x="462" y="133" width="31" height="192" fill="var(--yellow)"/><rect x="462" y="177" width="31" height="148" fill="var(--slate)"/>
        <rect x="501" y="133" width="31" height="192" fill="var(--yellow)"/><rect x="501" y="268" width="31" height="57" fill="var(--slate)"/>
      </g>
    </svg>
    <div class="footer"><span class="globe"></span>www.varnok.com<span class="rule"></span><span class="page">Page 05</span></div>
  </section>

  <!-- Partners -->
  <section class="slide c3 r2 light" style="background:#fff;color:var(--ink)">
    <div class="brand brand-top">VARNOK</div>
    <div class="abs" style="left:38px;top:20px;font-weight:700;font-size:17px"><span style="color:var(--yellow);font-weight:400;margin-right:8px">|</span>Our Partners<span style="color:var(--yellow);font-weight:400;margin-left:8px">|</span></div>
    <svg class="abs" style="left:0;top:0" width="669" height="376" viewBox="0 0 669 376">
      <g stroke="#cfcfcf" stroke-width="1">
        <line x1="177" y1="78" x2="177" y2="150"/><line x1="323" y1="78" x2="323" y2="150"/><line x1="475" y1="78" x2="475" y2="150"/>
        <line x1="177" y1="160" x2="177" y2="235"/><line x1="323" y1="160" x2="323" y2="235"/><line x1="475" y1="160" x2="475" y2="235"/>
        <line x1="177" y1="245" x2="177" y2="325"/><line x1="323" y1="245" x2="323" y2="325"/><line x1="475" y1="245" x2="475" y2="325"/>
        <line x1="18" y1="150" x2="167" y2="150"/><line x1="187" y1="150" x2="313" y2="150"/><line x1="333" y1="150" x2="465" y2="150"/><line x1="485" y1="150" x2="630" y2="150"/>
        <line x1="18" y1="237" x2="167" y2="237"/><line x1="187" y1="237" x2="313" y2="237"/><line x1="333" y1="237" x2="465" y2="237"/><line x1="485" y1="237" x2="630" y2="237"/>
      </g>
      <g fill="#2c2c2c">
        <rect x="50" y="95" width="92" height="24" rx="3"/>
        <circle cx="256" cy="105" r="22"/>
        <rect x="370" y="93" width="80" height="28" rx="14"/>
        <circle cx="555" cy="108" r="20"/>
        <rect x="60" y="180" width="80" height="20" rx="3"/>
        <rect x="225" y="178" width="64" height="24" rx="12"/>
        <rect x="372" y="178" width="64" height="32" rx="4"/>
        <rect x="518" y="182" width="76" height="18" rx="3"/>
        <rect x="52" y="268" width="86" height="22" rx="2"/>
        <circle cx="250" cy="280" r="24"/>
        <rect x="365" y="270" width="90" height="22" rx="11"/>
        <rect x="520" y="271" width="80" height="20" rx="10"/>
      </g>
    </svg>
    <div class="footer"><span class="globe"></span>www.varnok.com<span class="rule"></span><span class="page">Page 06</span></div>
  </section>

  <!-- Table -->
  <section class="slide c1 r3" style="background:#101a17">
    <div class="photo" role="img" aria-label="Green sports car in a dark garage" style="background:radial-gradient(ellipse at 55% 70%,#2c4a1e,#121d1a 60%,#0c1412)"></div>
    <div class="brand brand-top">VARNOK</div>
    <div class="abs" style="left:0;right:0;top:30px;text-align:center;font-family:'Cormorant Garamond',serif;font-size:19px;color:var(--yellow)"><span style="color:#fff;margin-right:8px">|</span>TABLE<span style="color:#fff;margin-left:8px">|</span></div>
    <p class="abs body-text" style="left:170px;right:170px;top:68px">Caerspiciatis unde omnis iste natus error slaskcit voluptatem accusantium doloremque laudantium.</p>
    <div class="th" style="left:60px;width:130px">FEATURE DESCRIPTION</div>
    <div class="th" style="left:195px;width:98px">COLUMN TITLE</div>
    <div class="th" style="left:298px;width:99px">COLUMN TITLE</div>
    <div class="th" style="left:402px;width:98px">COLUMN TITLE</div>
    <div class="th" style="left:506px;width:98px">COLUMN TITLE</div>
    <div class="row-label" style="top:156px">First Row</div>
    <div class="row-label" style="top:181px">Second Row</div>
    <div class="row-label" style="top:206px">Third Row</div>
    <div class="row-label" style="top:231px">Forth Row</div>
    <div class="row-label" style="top:256px">Fifth Row</div>
    <div class="row-label" style="top:281px">Sixth Row</div>
    <div class="row-label" style="top:306px">Seventh Row</div>
    <div class="dot" style="left:240px;top:159px"></div><div class="dot" style="left:343px;top:159px"></div><div class="dot" style="left:447px;top:159px"></div><div class="dot" style="left:551px;top:159px"></div>
    <div class="dot off" style="left:240px;top:184px"></div><div class="dot" style="left:343px;top:184px"></div><div class="dot" style="left:447px;top:184px"></div><div class="dot off" style="left:551px;top:184px"></div>
    <div class="dot" style="left:240px;top:209px"></div><div class="dot off" style="left:343px;top:209px"></div><div class="dot" style="left:447px;top:209px"></div><div class="dot" style="left:551px;top:209px"></div>
    <div class="dot" style="left:240px;top:234px"></div><div class="dot off" style="left:343px;top:234px"></div><div class="dot" style="left:447px;top:234px"></div><div class="dot" style="left:551px;top:234px"></div>
    <div class="dot off" style="left:240px;top:259px"></div><div class="dot" style="left:343px;top:259px"></div><div class="dot off" style="left:447px;top:259px"></div><div class="dot" style="left:551px;top:259px"></div>
    <div class="dot off" style="left:240px;top:284px"></div><div class="dot" style="left:343px;top:284px"></div><div class="dot off" style="left:447px;top:284px"></div><div class="dot" style="left:551px;top:284px"></div>
    <div class="dot" style="left:240px;top:309px"></div><div class="dot" style="left:343px;top:309px"></div><div class="dot off" style="left:447px;top:309px"></div><div class="dot" style="left:551px;top:309px"></div>
    <div class="footer"><span class="globe"></span>www.varnok.com<span class="rule"></span><span class="page">Page 07</span></div>
  </section>

  <!-- Contact -->
  <section class="slide c2 r3" style="background:#1f3f3a">
    <div class="photo" role="img" aria-label="Burgundy concept sports car in an arched hall" style="background:radial-gradient(ellipse at 58% 65%,#5a3a3a,#2a4a44 50%,#1a3632)"></div>
    <div class="abs" style="left:20px;top:18px;font-size:22px">Contact Varnok</div>
    <div class="abs" style="left:20px;top:52px;font-size:27px;font-weight:800;color:var(--yellow)">Let's make a plan.</div>
    <p class="abs" style="left:20px;top:98px;width:290px;font-size:10px;font-style:italic;line-height:17px">Caerspiciatis unde omnis iste natus error sit voluptatem accusantium doloremque lauda ntium tatam rasecseem aperiam, eaque ipsa quae ab illo inventore</p>
    <div class="abs" style="left:526px;top:38px;font-size:11.5px">www.varnok.com</div>
    <div class="abs" style="left:526px;top:60px;width:143px;height:1px;background:var(--gold)"></div>
    <svg class="abs" style="left:30px;top:341px" width="18" height="18" viewBox="0 0 24 24"><path fill="var(--yellow)" d="M6.6 10.8a15.1 15.1 0 0 0 6.6 6.6l2.2-2.2a1 1 0 0 1 1-.25 11.4 11.4 0 0 0 3.6.57 1 1 0 0 1 1 1V20a1 1 0 0 1-1 1A17 17 0 0 1 3 4a1 1 0 0 1 1-1h3.5a1 1 0 0 1 1 1c0 1.25.2 2.45.57 3.57a1 1 0 0 1-.25 1z"/></svg>
    <div class="abs" style="left:56px;top:336px;font-size:18px;font-weight:500">555.010.0199</div>
    <div class="brand abs" style="right:10px;top:300px;font-size:60px">VARNOK</div>
  </section>

  <!-- Closing -->
  <section class="slide c3 r3" style="background:var(--deep);display:flex;align-items:center;justify-content:center">
    <div class="brand" style="font-size:92px">VARNOK</div>
  </section>

</div>
</body>
</html>
```